E learning Platform for privacy

Current website is as below and its more of a shell.
I need someone to take the text and content and design it properly.
https://study.vornaquill.com/

After that, design has to be implemented with elementor and wordpress
https://elementor.com/

```html
<!DOCTYPE html>
<html lang="en">
<head>
<meta charset="utf-8">
<title>Vornaquill Learning Centre</title>
<link href="https://fonts.googleapis.com/css2?family=Raleway:wght@600;700;800&family=Montserrat:wght@400;500;600;700&family=Lato:wght@400;700&display=swap" rel="stylesheet">
<style>
:root{
  --brand:#e4521f;
  --brand-dark:#c9431a;
  --ink:#222222;
  --text:#555555;
  --muted:#777777;
  --panel:#efebea;
  --line:#e6e6e6;
  --footer:#0d0d0d;
  --white:#ffffff;
}
*{box-sizing:border-box;margin:0;padding:0}
html,body{width:1200px;height:4777px;overflow:hidden}
body{position:relative;background:var(--white);font-family:"Lato",sans-serif;color:var(--text)}
.abs{position:absolute}
.btn{display:inline-block;background:var(--brand);color:var(--white);font-family:"Montserrat",sans-serif;font-weight:600;font-size:14px;text-transform:uppercase;border-radius:26px;padding:15px 24px;letter-spacing:.2px}
.section-title{position:absolute;left:0;width:1200px;text-align:center;font-family:"Raleway",sans-serif;font-weight:800;font-size:38px;color:var(--brand);letter-spacing:.3px}
.dots{position:absolute;left:0;width:1200px;display:flex;justify-content:center;gap:5px}
.dots span{width:11px;height:11px;border-radius:50%;background:#555}
.dots span.on{background:var(--brand)}

/* header */
.topbar{top:0;left:0;width:1200px;height:7px;background:var(--brand)}
.site-header{top:7px;left:0;width:1200px;height:90px;background:var(--white)}
.brand{position:absolute;left:110px;top:22px;display:flex;align-items:center;gap:10px}
.brand-mark{width:18px;height:18px;background:var(--brand)}
.brand-name{font-family:"Montserrat",sans-serif;font-weight:700;font-size:22px;color:var(--brand);line-height:1}
.brand-sub{font-family:"Montserrat",sans-serif;font-weight:500;font-size:9px;letter-spacing:3px;color:#444;margin-top:4px}
.nav{position:absolute;left:363px;top:38px;display:flex;gap:0;font-family:"Montserrat",sans-serif;font-weight:500;font-size:16px;color:#222}
.nav a{margin-right:40px;text-decoration:none;color:inherit}
.nav a.active{color:var(--brand);border-bottom:2px solid var(--brand);padding-bottom:2px}
.nav .login{display:flex;align-items:center;gap:6px}

/* hero */
.hero{top:97px;left:0;width:1200px;height:558px;background:linear-gradient(100deg,#5c4e43 0%,#8a7868 35%,#c7bcb2 60%,#a49a92 100%)}
.hero-copy{position:absolute;left:114px;top:165px;color:var(--white)}
.hero-copy h1{font-family:"Montserrat",sans-serif;font-weight:700;font-size:50px;line-height:50px;text-transform:uppercase}
.hero-copy p{font-size:17px;margin:18px 0 28px}
.hero .dots{top:486px}
.hero .dots span{background:#444;width:12px;height:12px}
.hero .dots span.on{background:var(--brand)}

/* stats */
.stats{top:655px;left:0;width:1200px;height:106px;background:var(--brand);display:flex;color:var(--white);font-family:"Montserrat",sans-serif}
.stat{height:106px;display:flex;align-items:center;border-right:2px solid rgba(255,255,255,.45)}
.stat:last-child{border-right:none}
.stat svg{margin-right:14px}
.stat b{display:block;font-size:24px;font-weight:700;line-height:24px}
.stat small{font-size:16px;font-weight:500;text-transform:uppercase}

/* about */
.about-frame{left:118px;top:847px;width:444px;height:358px;border:4px solid var(--brand)}
.about-photo{left:127px;top:855px;width:425px;height:342px;background:linear-gradient(135deg,#d8d2cc,#8c8078 60%,#c9c1ba)}
.about-copy{left:612px;top:852px;width:470px}
.about-copy h2{font-family:"Raleway",sans-serif;font-weight:800;font-size:38px;color:var(--brand);margin-bottom:18px}
.about-copy p{font-size:15.5px;line-height:27px;color:var(--muted);margin-bottom:30px}

/* why */
.why-lead{top:1358px;left:0;width:1200px;text-align:center;font-size:15px;line-height:21px;color:#333}
.feature{position:absolute;width:280px;text-align:center}
.feature .icon{width:66px;height:66px;border:2px solid var(--brand);border-radius:50%;margin:0 auto 10px;display:flex;align-items:center;justify-content:center}
.feature h3{font-family:"Montserrat",sans-serif;font-weight:500;font-size:16px;line-height:21px;color:#111;text-transform:uppercase;margin-bottom:10px}
.feature p{font-size:14px;line-height:21px;color:#333;width:200px;margin:0 auto 10px}
.feature a{font-size:14px;color:var(--brand);text-decoration:none}

/* courses */
.course-photo{background:linear-gradient(120deg,#bfb6ad,#5f5650 45%,#d3ccc6)}
.course-panel{background:var(--panel);text-align:center}
.course-panel h3{font-family:"Montserrat",sans-serif;font-weight:600;font-size:15px;color:#111;text-transform:uppercase}
.course-meta{margin:22px auto 0;font-size:15px;color:#666;line-height:34px;text-align:left;display:inline-block}
.course-meta span{display:inline-block;width:110px}
.course-panel h4{font-family:"Montserrat",sans-serif;font-weight:600;font-size:15px;color:#111;margin-top:20px;text-transform:uppercase}
.course-panel p{font-size:15px;line-height:27px;color:#666;width:280px;margin:10px auto 24px}

/* testimonial */
.testimonial{left:205px;top:3415px;width:807px;height:345px;background:var(--white);box-shadow:0 0 10px rgba(0,0,0,.25);border-radius:4px;text-align:center}
.avatar{left:565px;top:3370px;width:82px;height:82px;border-radius:50%;background:linear-gradient(180deg,#6e7b86,#2b2f35)}
.testimonial h3{font-family:"Montserrat",sans-serif;font-weight:500;font-size:20px;color:#111;margin-top:62px}
.testimonial p{font-size:17px;line-height:31px;color:#333;width:640px;margin:20px auto 0;position:relative}
.quote{font-family:"Raleway",sans-serif;font-size:70px;color:#aaa;position:absolute;line-height:1}
.stars{margin-top:22px;display:flex;justify-content:center;gap:6px}

/* blog */
.blog-photo{height:258px;background:linear-gradient(135deg,#2c6f8e,#8fc5d6 50%,#244a5e)}
.blog-photo.alt{background:linear-gradient(135deg,#e5e7ea,#9aa2ab 55%,#4b5560)}
.blog-meta{position:absolute;width:160px;height:140px;background:var(--white);box-shadow:0 0 6px rgba(0,0,0,.25);padding:14px 0 0 22px;font-size:17px;color:var(--brand);line-height:38px}
.blog-meta div{display:flex;align-items:center;gap:8px}
.blog-text{position:absolute;width:300px;font-size:14.5px;line-height:28px}
.blog-text .more{color:#777}
.arrow{width:36px;height:36px;border-radius:50%;background:#666;display:flex;align-items:center;justify-content:center}

/* footer */
.site-footer{top:4420px;left:0;width:1200px;height:357px;background:var(--footer);color:var(--white)}
.site-footer h4{font-family:"Montserrat",sans-serif;font-weight:600;font-size:16px;margin-bottom:12px}
.site-footer .col{position:absolute;top:48px;font-size:15px;line-height:26px}
.contact-row{display:flex;gap:10px;margin-bottom:8px}
.contact-row svg{flex:none;margin-top:6px}
.news-input{width:264px;height:42px;background:var(--white);color:#777;font-size:14px;padding:12px 8px;margin-bottom:22px}
.powered{position:absolute;left:400px;top:235px;display:flex;align-items:center;gap:20px;font-family:"Montserrat",sans-serif}
.live-chat{position:absolute;left:873px;top:226px;width:204px;height:48px;background:var(--brand);border-radius:24px;font-family:"Montserrat",sans-serif;font-weight:500;font-size:15px;display:flex;align-items:center;padding-left:85px}
.chat-avatar{position:absolute;left:-4px;top:-6px;width:60px;height:60px;border-radius:50%;background:linear-gradient(180deg,#8d96a0,#3a4048);border:3px solid var(--white)}
.socials{position:absolute;left:125px;top:292px;display:flex;gap:16px}
.socials span{width:12px;height:12px;border-radius:50%;background:var(--brand)}
.copyright{position:absolute;left:0;width:1200px;top:312px;text-align:center;font-size:11px}
.page-code{position:absolute;left:1120px;top:312px;font-size:11px}
</style>
</head>
<body>

<div class="abs topbar"></div>
<header class="abs site-header">
  <div class="brand">
    <span class="brand-mark"></span>
    <div>
      <div class="brand-name">VORNAQUILL</div>
      <div class="brand-sub">LEARNING CENTRE</div>
    </div>
  </div>
  <nav class="nav">
    <a class="active">HOME</a>
    <a>ABOUT US</a>
    <a>BLOGS</a>
    <a>COURSES</a>
    <a>CONTACT US</a>
    <a class="login"><svg width="12" height="14" viewBox="0 0 12 14"><circle cx="6" cy="4" r="3.2" fill="#e4521f"/><path d="M0 14c0-4 2.6-6 6-6s6 2 6 6z" fill="#e4521f"/></svg>LOGIN / REGISTER</a>
  </nav>
</header>

<section class="abs hero" role="img" aria-label="Student working on a laptop in a library, taking notes">
  <div class="hero-copy">
    <h1>Data Protection<br>Excellence</h1>
    <p>Largest online e-learning resource for data protection &amp; privacy</p>
    <span class="btn">Get Started</span>
  </div>
  <div class="dots"><span class="on"></span><span></span><span></span><span></span></div>
</section>

<section class="abs stats">
  <div class="stat" style="width:487px;padding-left:135px">
    <svg width="54" height="40" viewBox="0 0 54 40"><path d="M27 2 2 13l25 11 25-11z" fill="#fff"/><path d="M12 19v10c0 4 7 8 15 8s15-4 15-8V19l-15 7z" fill="#fff"/><path d="M48 15v14" stroke="#fff" stroke-width="2"/></svg>
    <div><b>6,375</b><small>Enrolled Students</small></div>
  </div>
  <div class="stat" style="width:358px;padding-left:105px">
    <svg width="32" height="38" viewBox="0 0 32 38"><rect x="3" y="3" width="26" height="32" fill="none" stroke="#fff" stroke-width="3"/><rect x="9" y="9" width="10" height="12" fill="#fff"/><path d="M9 26h14M9 30h14" stroke="#fff" stroke-width="2"/></svg>
    <div><b>114</b><small>Lessons</small></div>
  </div>
  <div class="stat" style="width:355px;padding-left:38px">
    <svg width="48" height="30" viewBox="0 0 48 30"><rect x="1" y="2" width="32" height="26" rx="3" fill="#fff"/><path d="M35 15 47 5v20z" fill="#fff"/></svg>
    <div><b>169</b><small>Videos</small></div>
  </div>
</section>

<div class="abs about-frame"></div>
<div class="abs about-photo" role="img" aria-label="Student with headphones writing notes beside a laptop"></div>
<div class="abs about-copy">
  <h2>ABOUT US</h2>
  <p>Lorem ipsum dolor sit amet, consectetur adipiscing elit, sed do eiusmod tempor incididunt ut labore et dolore magna aliqua. Ut enim ad minim veniam, quis nostrud exercitation ullamco laboris nisi ut aliquip ex ea commodo consequat. Duis aute irure dolor in reprehenderit in voluptate velit esse cillum dolore eu fugiat nulla pariatur.</p>
  <span class="btn" style="margin-left:-8px">Read More</span>
</div>

<h2 class="section-title" style="top:1305px">WHY THE (VORNAQUILL) LEARNING CENTRE?</h2>
<p class="abs why-lead">Our mission at the Vornaquill Learning Centre is to provide business and job opportunities,<br>as well as to enhance personal and career advancement for data protection / privacy professionals.</p>

<div class="feature" style="left:108px;top:1492px">
  <div class="icon"><svg width="36" height="36" viewBox="0 0 36 36" fill="none" stroke="#e4521f" stroke-width="2"><path d="M11 4a6 6 0 0 1 6 6c0 5-6 11-6 11S5 15 5 10a6 6 0 0 1 6-6z"/><circle cx="11" cy="10" r="2"/><path d="M26 14a5 5 0 0 1 5 5c0 4-5 9-5 9s-5-5-5-9a5 5 0 0 1 5-5z"/><path d="M11 24c2 6 10 6 12 8" stroke-dasharray="2 2"/></svg></div>
  <h3>Comprehensive<br>Roadmap</h3>
  <p>Our objective is to provide a comprehensive competency roadmap, instead of one-off courses, whether you are</p>
  <a>Read More</a>
</div>
<div class="feature" style="left:455px;top:1492px">
  <div class="icon"><svg width="34" height="34" viewBox="0 0 34 34" fill="none" stroke="#e4521f" stroke-width="2"><rect x="4" y="4" width="26" height="26"/><path d="M4 12h26M12 4v26M16 26l10-10M18 18h8v8"/></svg></div>
  <h3>Operational<br>Perspective</h3>
  <p>We cover a broad range of data protection topics from both a legal and operational perspective, covering</p>
  <a>Read More</a>
</div>
<div class="feature" style="left:802px;top:1492px">
  <div class="icon"><svg width="30" height="36" viewBox="0 0 30 36" fill="none" stroke="#e4521f" stroke-width="2"><path d="M3 2h18l6 6v26H3z"/><path d="M8 10h12M8 15h14M8 20h14"/><circle cx="15" cy="27" r="3"/></svg></div>
  <h3>Academic &amp; International<br>Certification</h3>
  <p>We partner with prominent universities in the region as well as international certification bodies such as</p>
  <a>Read More</a>
</div>
<div class="feature" style="left:108px;top:1766px">
  <div class="icon"><svg width="36" height="36" viewBox="0 0 36 36" fill="none" stroke="#e4521f" stroke-width="2"><circle cx="18" cy="9" r="5"/><path d="M9 22c0-5 4-8 9-8s9 3 9 8"/><rect x="5" y="22" width="26" height="8"/><path d="M10 30v4M26 30v4"/></svg></div>
  <h3>Modular Approach<br>&amp; Flexibility</h3>
  <p>All our courses are modular in nature to cater to the busy professional, meaning that you can take the</p>
  <a>Read More</a>
</div>
<div class="feature" style="left:455px;top:1766px">
  <div class="icon"><svg width="36" height="36" viewBox="0 0 36 36" fill="none" stroke="#e4521f" stroke-width="2"><circle cx="12" cy="8" r="4"/><circle cx="26" cy="10" r="3"/><rect x="6" y="17" width="24" height="14"/><path d="M12 24h12"/></svg></div>
  <h3>Network with<br>Other Peers</h3>
  <p>Participate in our online communities and discussion rooms and your network with other like-minded</p>
  <a>Read More</a>
</div>
<div class="feature" style="left:802px;top:1766px">
  <div class="icon"><svg width="36" height="36" viewBox="0 0 36 36" fill="none" stroke="#e4521f" stroke-width="2"><circle cx="18" cy="12" r="5"/><path d="M8 32c0-7 4-12 10-12s10 5 10 12"/><circle cx="7" cy="7" r="3"/><circle cx="29" cy="7" r="3"/></svg></div>
  <h3>Business and Job<br>Opportunities</h3>
  <p>Collaborate with other professionals on potential business opportunities whether it relates to</p>
  <a>Read More</a>
</div>
<div class="dots" style="top:2020px"><span class="on"></span><span></span></div>

<h2 class="section-title" style="top:2158px">FEATURED COURSES</h2>

<div class="abs course-photo" style="left:0;top:2250px;width:755px;height:465px" role="img" aria-label="Student in headphones studying at a laptop"></div>
<div class="abs course-panel" style="left:755px;top:2250px;width:445px;height:465px;padding-top:30px">
  <h3>How to Scale Social Impact</h3>
  <div class="course-meta">
    <div><span>Course Type</span>: &nbsp;Instructor-paced</div>
    <div><span>Start Date</span>: &nbsp;Dec 19, 2019</div>
    <div><span>End Date</span>: &nbsp;Jan 02, 2021</div>
    <div>Course Duration: &nbsp;55 Weeks</div>
  </div>
  <h4>Course Instructors</h4>
  <p>Lorem ipsum dolor sit amet, conse ctetur adipiscing elit, sed do eius mod tempo</p>
  <span class="btn">Read More</span>
</div>

<div class="abs course-panel" style="left:0;top:2715px;width:447px;height:468px;padding-top:30px">
  <h3>Kestrel Demonstration Course</h3>
  <div class="course-meta">
    <div><span>Course Type</span>: &nbsp;Instructor-paced</div>
    <div><span>Start Date</span>: &nbsp;Dec 17, 2019</div>
    <div><span>End Date</span>: &nbsp;Jul 03, 2021</div>
    <div>Course Duration: &nbsp;81 Weeks</div>
  </div>
  <h4>Course Instructors</h4>
  <p>Lorem ipsum dolor sit amet, conse ctetur adipiscing elit, sed do eius mod tempo</p>
  <span class="btn">Read More</span>
</div>
<div class="abs course-photo" style="left:447px;top:2715px;width:753px;height:468px;background:linear-gradient(120deg,#5b5550,#b5aba3 50%,#e3ddd7)" role="img" aria-label="Student with headphones writing notes at a laptop"></div>
<div class="dots" style="top:3207px"><span class="on"></span><span></span></div>

<h2 class="section-title" style="top:3265px">CLIENTS TESTIMONIAL</h2>
<div class="abs testimonial">
  <h3>John doe</h3>
  <p><span class="quote" style="left:-42px;top:-12px">&ldquo;</span>Lorem ipsum dolor sit amet, consectetur adipiscing elit, sed do eiusmod tempor incididunt ut labore et dolore magna aliqua. Ut enim ad minim veniam, quis nostrud exercitation ullamco laboris nisi ut aliquip ex ea commodo conseq uatDuis aute irure dolor in reprehenderit in voluptate velit<span class="quote" style="right:0;bottom:-36px">&rdquo;</span></p>
  <div class="stars">
    <svg width="130" height="24" viewBox="0 0 130 24"><g fill="#f08a1c"><path id="st" d="M12 1l3.3 7 7.7.9-5.7 5.2 1.5 7.6L12 18l-6.8 3.7 1.5-7.6L1 8.9 8.7 8z"/><use href="#st" x="26"/><use href="#st" x="52"/><use href="#st" x="78"/><use href="#st" x="104"/></g></svg>
  </div>
</div>
<div class="abs avatar" role="img" aria-label="Client portrait"></div>
<div class="dots" style="top:3788px"><span class="on"></span><span style="background:#fff;border:2px solid var(--brand)"></span><span class="on"></span></div>

<h2 class="section-title" style="top:3880px">LATEST BLOG</h2>

<div class="abs blog-photo" style="left:110px;top:3962px;width:478px" role="img" aria-label="Hands typing on a laptop with a digital padlock overlay"></div>
<div class="blog-meta" style="left:118px;top:4190px">
  <div><svg width="15" height="15" viewBox="0 0 15 15"><rect x="1" y="3" width="13" height="11" fill="none" stroke="#e4521f" stroke-width="2"/><path d="M1 6h13" stroke="#e4521f" stroke-width="2"/></svg>14-01-2020</div>
  <div><svg width="14" height="15" viewBox="0 0 14 15"><circle cx="7" cy="4" r="3.5" fill="#e4521f"/><path d="M0 15c0-4 3-6 7-6s7 2 7 6z" fill="#e4521f"/></svg>By John Doe</div>
  <div><svg width="16" height="14" viewBox="0 0 16 14"><ellipse cx="8" cy="6" rx="8" ry="6" fill="#e4521f"/><path d="M3 10l-2 4 5-2z" fill="#e4521f"/></svg>Comment(10)</div>
</div>
<div class="blog-text" style="left:300px;top:4235px;color:var(--brand)">Lorem ipsum dolor sit amet, consectetur a dipiscing elit, sed do eiusmod tempor incid<br><span style="color:var(--brand)">Continue Reading</span></div>

<div class="abs blog-photo alt" style="left:608px;top:3962px;width:478px" role="img" aria-label="Business analyst reviewing charts and a world map on a laptop"></div>
<div class="blog-meta" style="left:616px;top:4190px">
  <div><svg width="15" height="15" viewBox="0 0 15 15"><rect x="1" y="3" width="13" height="11" fill="none" stroke="#e4521f" stroke-width="2"/><path d="M1 6h13" stroke="#e4521f" stroke-width="2"/></svg>14-01-2020</div>
  <div><svg width="14" height="15" viewBox="0 0 14 15"><circle cx="7" cy="4" r="3.5" fill="#e4521f"/><path d="M0 15c0-4 3-6 7-6s7 2 7 6z" fill="#e4521f"/></svg>By John Doe</div>
  <div><svg width="16" height="14" viewBox="0 0 16 14"><ellipse cx="8" cy="6" rx="8" ry="6" fill="#e4521f"/><path d="M3 10l-2 4 5-2z" fill="#e4521f"/></svg>Comment(10)</div>
</div>
<div class="blog-text" style="left:797px;top:4235px;color:#777">Lorem ipsum dolor sit amet, consectetur adipiscing elit, sed do eiusmod tempor i<br><span class="more">Continue Reading</span></div>

<div class="abs arrow" style="left:90px;top:4062px"><svg width="10" height="14" viewBox="0 0 10 14"><path d="M8 1 2 7l6 6" fill="none" stroke="#fff" stroke-width="2"/></svg></div>
<div class="abs arrow" style="left:1067px;top:4062px"><svg width="10" height="14" viewBox="0 0 10 14"><path d="M2 1l6 6-6 6" fill="none" stroke="#fff" stroke-width="2"/></svg></div>

<footer class="abs site-footer">
  <div class="col" style="left:116px;width:280px">
    <h4>CONTACT INFO</h4>
    <div class="contact-row"><svg width="10" height="14" viewBox="0 0 10 14"><path d="M5 0a5 5 0 0 1 5 5c0 4-5 9-5 9S0 9 0 5a5 5 0 0 1 5-5z" fill="#e4521f"/><circle cx="5" cy="5" r="2" fill="#0d0d0d"/></svg><span>418 Harwell Row Suite 210, Brookmere, OR 97321, USA</span></div>
    <div class="contact-row"><svg width="14" height="11" viewBox="0 0 14 11"><rect width="14" height="11" fill="#e4521f"/><path d="M0 0l7 6 7-6" fill="none" stroke="#0d0d0d" stroke-width="1.5"/></svg><span>support@study.vornaquill.com</span></div>
    <div class="contact-row"><svg width="12" height="12" viewBox="0 0 12 12"><path d="M2 0l3 3-1.5 2a7 7 0 0 0 3.5 3.5L9 7l3 3-2 2C5 12 0 7 0 2z" fill="#e4521f"/></svg><span>+1 (555) 014 27 83</span></div>
  </div>
  <div class="col" style="left:527px">
    <h4>QUICK LINK</h4>
    <div>Home</div><div>About Us</div><div>Blogs</div><div>Courses</div><div>Contact Us</div>
  </div>
  <div class="col" style="left:806px">
    <h4>NEWSLETTERS</h4>
    <div class="news-input">Enter The Email</div>
    <span class="btn" style="font-size:14px;padding:14px 24px">Subscribe</span>
  </div>
  <div class="powered">
    <span style="font-weight:700;font-size:16px">POWERED BY</span>
    <span style="font-weight:700;font-size:24px;color:var(--brand)">Lumora</span>
    <span style="font-weight:700;font-size:20px;color:var(--brand)">Kestrelbase</span>
  </div>
  <div class="live-chat"><span class="chat-avatar" role="img" aria-label="Support agent portrait"></span>LIVE CHAT</div>
  <div class="socials"><span></span><span></span><span></span></div>
  <div class="copyright">&copy; Copy Rights Vornaquill Learning Centre &nbsp; | &nbsp; All Rights Reserved</div>
  <div class="page-code">C 43</div>
</footer>

</body>
</html>
```